Redesign Of Current Landing Page

I need to redesign this landing page https://www.brightlanepromo.biz/?page=landing&landing=23 (Please do not opt in because when you do it will show you the home page. Please clear your cookies before going to this url above to view the 1 page landing page.)

Please use my updated website as a reference for colors and logo.
http://sitecradlewerk.com/dh/bpq/index.html

I would like the call to action to be a button that opens into a lead form...

Button would be "Download Samples"

Target Market(s)

small business owners

Industry/Entity Type

Marketing

Number of Pages Required

1 page

Colors

Designer to choose colors to be used in the design.

Requirements
Must have
• must be full responsive on all devices
Nice to have
• must have a legitimate professional apeal to it
Should not have
• open

```html
<!DOCTYPE html>
<html lang="en">
<head>
<meta charset="utf-8">
<title>Brightlane Promo Incentive</title>
<link href="https://fonts.googleapis.com/css2?family=Lato:wght@400;700;900&family=Open+Sans:ital,wght@0,400;0,600;0,700;1,400;1,600&display=swap" rel="stylesheet">
<style>
:root{
  --blue:#1a73c9;
  --blue-dark:#0f5fae;
  --orange:#f7a81b;
  --ink:#222;
  --muted:#555;
  --footer:#1c1c1c;
  --white:#fff;
}
*{box-sizing:border-box;margin:0;padding:0}
html,body{width:1200px;height:2647px;overflow:hidden}
body{font-family:"Open Sans",Arial,sans-serif;color:var(--ink);background:var(--white);position:relative}
.abs{position:absolute}
h1,h2,h3{font-family:"Lato",Arial,sans-serif}

/* header */
.site-header{position:absolute;top:0;left:0;width:1200px;height:85px;border-top:4px solid var(--blue-dark);background:var(--white);box-shadow:0 2px 4px rgba(0,0,0,.15);z-index:2}
.brand{position:absolute;left:99px;top:18px;display:flex;align-items:center;gap:10px}
.brand-dot{width:42px;height:42px;border-radius:50%;background:var(--blue)}
.brand-name{font-family:"Lato",sans-serif;font-weight:900;font-size:34px;color:#111;letter-spacing:1px}
.main-nav{position:absolute;right:86px;top:33px;display:flex;gap:34px;font-family:"Lato",sans-serif;font-size:15px;font-weight:700;color:#222}
.main-nav .active{color:var(--orange)}
.search-icon{position:absolute;right:67px;top:34px}

/* hero */
.hero{position:absolute;top:85px;left:0;width:1200px;height:435px;background:linear-gradient(135deg,#5c5a56 0%,#8d8a84 40%,#6f7a86 70%,#3e3f41 100%)}
.hero-title{position:absolute;top:190px;width:100%;text-align:center;font-size:52px;font-weight:700;color:var(--white);letter-spacing:.5px}
.hero-sub{position:absolute;top:264px;width:100%;text-align:center;font-size:20px;font-weight:600;color:var(--white)}
.btn{display:inline-block;background:var(--orange);color:var(--white);font-family:"Open Sans",sans-serif;font-weight:700;text-align:center;border-radius:4px}
.hero-btn{position:absolute;left:496px;top:318px;width:206px;height:46px;line-height:46px;font-size:16px}
.dots{position:absolute;display:flex;gap:6px}
.dots span{width:13px;height:13px;border-radius:50%;border:2px solid var(--white)}
.dots span.on{background:var(--white)}

/* welcome */
.welcome-title{position:absolute;left:99px;top:588px;font-size:27px;font-weight:700;line-height:36px;color:#222}
.welcome-text{position:absolute;left:99px;top:675px;width:492px;font-size:12.5px;line-height:27px;color:var(--muted)}
.welcome-text p+p{margin-top:20px}
.btn-outline{position:absolute;left:99px;top:851px;width:122px;height:34px;line-height:31px;border:1.5px solid #999;border-radius:4px;color:var(--orange);font-size:12px;font-weight:700;text-align:center}
.video-frame{position:absolute;left:639px;top:593px;width:465px;height:285px;border:1px solid #ccc;padding:5px;background:var(--white)}
.video-media{width:100%;height:100%;background:radial-gradient(circle at 55% 40%,#a7c4dc 0%,#4a6a8c 45%,#253447 100%);position:relative}
.play{position:absolute;left:207px;top:108px;width:58px;height:58px;border-radius:50%;background:#1d1d1d}

/* how */
.how{position:absolute;top:958px;left:0;width:1200px;height:371px;background:linear-gradient(120deg,#4a4540 0%,#6b635b 45%,#8b857d 70%,#3c3a38 100%)}
.how h2{position:absolute;top:64px;width:100%;text-align:center;font-size:27px;font-weight:700;color:var(--white)}
.how p{position:absolute;top:118px;left:245px;width:710px;text-align:center;font-size:14px;line-height:28.5px;color:#f2f2f2}
.how-btn{position:absolute;left:515px;top:263px;width:170px;height:48px;line-height:48px;font-size:15px}

/* why */
.why-title{position:absolute;top:1405px;width:100%;text-align:center;font-size:27px;font-weight:700;color:#222}
.feature-circle{position:absolute;width:98px;height:98px;border-radius:50%;border:2.5px solid var(--blue);display:flex;align-items:center;justify-content:center}
.feature-label{position:absolute;font-size:16px;line-height:26px;color:#444;width:260px}
.feature-label.left{text-align:right}

/* testimonials */
.testimonials{position:absolute;top:1910px;left:0;width:1200px;height:379px;background:var(--blue)}
.testimonials h2{position:absolute;top:65px;width:100%;text-align:center;font-size:26px;font-weight:700;color:var(--white)}
.quote-mark{position:absolute;left:106px;top:112px;width:126px;height:126px;border-radius:50%;background:#e4e4e4}
.person{position:absolute;left:180px;top:121px;width:108px;height:108px;border-radius:50%;background:linear-gradient(160deg,#d9dde3,#8a96a6);border:3px solid var(--white)}
.quote-text{position:absolute;left:319px;top:124px;width:780px;font-size:12.4px;line-height:27px;font-style:italic;color:var(--white)}
.quote-name{position:absolute;left:319px;top:256px;font-family:"Lato",sans-serif;font-weight:900;font-size:15px;color:var(--white)}
.quote-place{position:absolute;left:319px;top:278px;font-style:italic;font-size:14px;color:var(--white)}

/* footer */
.site-footer{position:absolute;top:2289px;left:0;width:1200px;height:358px;background:var(--footer);color:var(--white)}
.footer-brand{position:absolute;left:99px;top:125px;display:flex;align-items:center;gap:12px}
.footer-brand .brand-dot{width:60px;height:60px}
.footer-brand .brand-name{color:var(--white);font-size:46px}
.footer-col h3{font-size:19px;font-weight:700;margin-bottom:22px}
.footer-col{position:absolute;top:58px;font-size:12.5px}
.link-list li{list-style:none;line-height:22px}
.news-text{line-height:22px;width:260px}
.email-field{margin-top:14px;width:255px;height:36px;background:var(--white);color:#555;padding-left:12px;line-height:36px;font-size:12px}
.sub-btn{margin-top:18px;width:86px;height:30px;line-height:30px;font-size:11px;border-radius:4px}
.contact-row{display:flex;gap:14px;margin-bottom:15px;line-height:18px}
.contact-row svg{flex:none;margin-top:2px}
.footer-rule{position:absolute;left:99px;right:99px;top:284px;border-top:1px solid #3a3a3a}
.copyright{position:absolute;left:99px;top:312px;font-size:12px}
.social{position:absolute;right:99px;top:307px;display:flex;gap:8px}
.social span{width:28px;height:28px;border-radius:50%;border:1.5px solid #ccc}
</style>
</head>
<body>

<header class="site-header">
  <div class="brand"><span class="brand-dot"></span><span class="brand-name">BLPG</span></div>
  <nav class="main-nav">
    <span class="active">HOME</span><span>OUR INCENTIVES</span><span>SAMPLES</span><span>AFFILIATES</span><span>FAQ</span><span>CONTACT</span>
  </nav>
  <svg class="search-icon" width="16" height="16" viewBox="0 0 16 16"><circle cx="6.5" cy="6.5" r="5" fill="none" stroke="#222" stroke-width="2.2"/><line x1="10.3" y1="10.3" x2="15" y2="15" stroke="#222" stroke-width="2.5"/></svg>
</header>

<section class="hero" role="img" aria-label="Photo of people working at a desk with a laptop and paperwork">
  <h1 class="hero-title">BRIGHTLANE PROMO INCENTIVE</h1>
  <p class="hero-sub">Attract more customers who spend more money with your business more often!</p>
  <span class="btn hero-btn">DOWNLOAD SAMPLES</span>
  <div class="dots" style="left:565px;top:368px"><span class="on"></span><span></span><span></span><span></span></div>
</section>

<section class="welcome">
  <h2 class="welcome-title">WELCOME TO<br>BRIGHTLANE PROMO INCENTIVE</h2>
  <div class="welcome-text">
    <p>&nbsp;Imagine being able to create exciting give away promotions that will boost your sales without ever having to worry about cost.</p>
    <p>Brightlane Promo Group, Inc. provides high-perceived value promotional incentives to businesses that want to advertise an exciting Give Away that will instantly attract more customers from your existing advertising efforts.</p>
  </div>
  <span class="btn-outline">READ MORE &gt;&gt;</span>
  <div class="video-frame">
    <div class="video-media" role="img" aria-label="Video still of open hands holding a glowing digital network">
      <span class="play"><svg width="58" height="58" viewBox="0 0 58 58"><path d="M23 18 L40 29 L23 40 Z" fill="#fff"/></svg></span>
    </div>
  </div>
</section>

<section class="how" role="img" aria-label="Background photo of hands typing on a laptop">
  <h2>HOW CAN WE DO IT?</h2>
  <p>We help fill empty rooms for thousands of hotels and resorts in hundreds of destinations around the world as well as the major cruise lines. Hotels and resorts are rarely full so when we place someone in their empty rooms, they end up making it up when travelers spend money on room service, spa services, eat at their in-house restaurants, casino and take advantage of other amenities that drive revenue.</p>
  <span class="btn how-btn">READ MORE &gt;&gt;</span>
</section>

<section class="why">
  <h2 class="why-title">WHY OFFER INCENTIVES TO CUSTOMERS?</h2>

  <div class="feature-label left" style="left:169px;top:1508px">Increase Responses From Your Existing Ads</div>
  <div class="feature-circle" style="left:463px;top:1486px">
    <svg width="46" height="40" viewBox="0 0 46 40"><path d="M4 14 h8 l20 -11 v32 l-20 -11 h-8 z" fill="#f7a81b"/><rect x="10" y="24" width="7" height="12" fill="#f7a81b"/><path d="M37 12 l6 -4 M38 19 h7 M37 26 l6 4" stroke="#f7a81b" stroke-width="2.5"/></svg>
  </div>
  <div class="feature-circle" style="left:634px;top:1486px">
    <svg width="48" height="40" viewBox="0 0 48 40"><path d="M3 2 v35 h43" fill="none" stroke="#f7a81b" stroke-width="3"/><rect x="10" y="20" width="6" height="14" fill="#f7a81b"/><rect x="19" y="12" width="6" height="22" fill="#f7a81b"/><rect x="28" y="16" width="6" height="18" fill="#f7a81b"/><rect x="37" y="6" width="6" height="28" fill="#f7a81b"/></svg>
  </div>
  <div class="feature-label" style="left:769px;top:1508px">Insure The Sale Over Your Competition</div>

  <div class="feature-label left" style="left:169px;top:1628px">#1 Sales Closing Tool - Gift w/ Purchase</div>
  <div class="feature-circle" style="left:463px;top:1607px">
    <svg width="50" height="46" viewBox="0 0 50 46"><circle cx="18" cy="26" r="11" fill="none" stroke="#f7a81b" stroke-width="7" stroke-dasharray="5 3.6"/><circle cx="18" cy="26" r="4" fill="#f7a81b"/><circle cx="37" cy="12" r="7" fill="none" stroke="#f7a81b" stroke-width="5" stroke-dasharray="4 2.6"/><circle cx="38" cy="36" r="6" fill="none" stroke="#f7a81b" stroke-width="4" stroke-dasharray="3.5 2.4"/></svg>
  </div>
  <div class="feature-circle" style="left:634px;top:1607px">
    <svg width="44" height="40" viewBox="0 0 44 40"><rect x="14" y="3" width="16" height="8" rx="2" fill="none" stroke="#f7a81b" stroke-width="3"/><rect x="2" y="10" width="40" height="28" rx="3" fill="#f7a81b"/><rect x="9" y="10" width="3" height="28" fill="#fff"/><rect x="32" y="10" width="3" height="28" fill="#fff"/></svg>
  </div>
  <div class="feature-label" style="left:769px;top:1628px">Boost Repeat and Referral Business</div>

  <div class="feature-label left" style="left:169px;top:1749px">Build Brand Awareness and Trust</div>
  <div class="feature-circle" style="left:463px;top:1727px">
    <svg width="42" height="42" viewBox="0 0 42 42"><rect x="2" y="18" width="8" height="20" fill="#f7a81b"/><path d="M13 18 l8 -14 c3 -2 6 0 5 4 l-2 8 h12 c3 0 5 3 4 6 l-4 14 c-1 2 -2 3 -5 3 h-18 z" fill="#f7a81b"/></svg>
  </div>
  <div class="feature-circle" style="left:634px;top:1727px">
    <svg width="48" height="34" viewBox="0 0 48 34"><rect x="2" y="2" width="44" height="30" fill="#f7a81b"/><rect x="6" y="6" width="36" height="22" fill="none" stroke="#fff" stroke-width="2"/><circle cx="24" cy="17" r="8" fill="#fff"/><rect x="22" y="12" width="4" height="10" fill="#f7a81b"/></svg>
  </div>
  <div class="feature-label" style="left:769px;top:1749px">Improve Retention Rates</div>
</section>

<section class="testimonials">
  <h2>TESTIMONIALS</h2>
  <div class="quote-mark"><svg width="126" height="126" viewBox="0 0 126 126"><text x="22" y="100" font-family="Georgia,serif" font-size="100" fill="#c9c9c9">&#8220;</text></svg></div>
  <div class="person" role="img" aria-label="Portrait of the customer giving the testimonial"></div>
  <p class="quote-text">I began using your incentives two years ago to boost lead generation efforts. I have experienced a 63% increase in lead captures. And, even more importantly, my sales have increased as well. The ability to offer unlimited certificates and not having to pay for each certificate I give away is perhaps the best feature of the program, but having the flexibility to email or print certificates for my customers is also wonderful. I even use your html banners to automate my promotions right on my website!</p>
  <div class="quote-name">DANA R.</div>
  <div class="quote-place">Fairview, TN</div>
  <div class="dots" style="left:577px;top:316px"><span class="on"></span><span></span><span></span></div>
</section>

<footer class="site-footer">
  <div class="footer-brand"><span class="brand-dot"></span><span class="brand-name">BLPG</span></div>

  <div class="footer-col" style="left:399px">
    <h3>Information</h3>
    <ul class="link-list"><li>Home</li><li>About Us</li><li>Our Team</li><li>Services</li><li>Careers</li><li>Blog</li><li>Contact Us</li></ul>
  </div>

  <div class="footer-col" style="left:563px">
    <h3>Newsletter Subscription</h3>
    <p class="news-text">Register your Email Address to get Information about us</p>
    <div class="email-field">Email Address</div>
    <div class="btn sub-btn">SUBSCRIBE</div>
  </div>

  <div class="footer-col" style="left:875px">
    <h3>Contact Us</h3>
    <div class="contact-row"><svg width="12" height="16" viewBox="0 0 12 16"><path d="M6 0 a6 6 0 0 1 6 6 c0 4 -6 10 -6 10 s-6 -6 -6 -10 a6 6 0 0 1 6 -6z" fill="#fff"/><circle cx="6" cy="6" r="2.2" fill="#1c1c1c"/></svg><span>240 N. Alder St. Suite 800<br>Carson City, NV 89701</span></div>
    <div class="contact-row"><svg width="14" height="14" viewBox="0 0 14 14"><path d="M3 0 l3 3 -2 2 c1 2 3 4 5 5 l2 -2 3 3 -2 3 c-6 0 -12 -6 -12 -12z" fill="#fff"/></svg><span>1 800 555 0142</span></div>
    <div class="contact-row"><svg width="14" height="14" viewBox="0 0 14 14"><rect x="3" y="0" width="8" height="4" fill="#fff"/><rect x="0" y="5" width="14" height="9" rx="1" fill="#fff"/><rect x="4" y="8" width="6" height="3" fill="#1c1c1c"/></svg><span>1 800 555 0187</span></div>
    <div class="contact-row"><svg width="14" height="11" viewBox="0 0 14 11"><rect width="14" height="11" rx="1" fill="#fff"/><path d="M0 1 l7 5 7 -5" fill="none" stroke="#1c1c1c" stroke-width="1.4"/></svg><span>info@brightlanepromo.biz</span></div>
  </div>

  <div class="footer-rule"></div>
  <p class="copyright">Copyrights © 2017, Brightlane Promo Group, Inc. All rights reserved.</p>
  <div class="social"><span></span><span></span><span></span><span></span></div>
</footer>

</body>
</html>
```